Elevating our current Business Card Design

We want to elevate our current business card with a new design to look like a zenith 300 company. We are a premium lubricant distributor (oil and grease).
We need 2 versions, version 1 is as per the uploaded a copy of our current business card with the English version.
For our Chinese version we need to use the front to be English in English and have the back of the card designed exactly like the front for all info to be in Chinese.
The design template needs to be such that we can amend the template with adding different information for each person's card.
The background colour of the card can be changed- we just need to clearly see all information on the card and logos.
The QJR and Ember steady logos cannot have any colour or display changes- only use the logos attached.
All logos need to be included and all information from the attached current card

```html
<!DOCTYPE html>
<html lang="en">
<head>
<meta charset="utf-8">
<title>Kelvane Business Card</title>
<link rel="stylesheet" href="https://fonts.googleapis.com/css2?family=Exo+2:wght@500;600;700&family=Open+Sans:wght@400;600&display=swap">
<style>
  :root {
    --stage: #232323;
    --card: #1f1f22;
    --red: #e92b26;
    --red-deep: #a3181c;
    --silver: #c9c9cc;
    --gold: #f0b62e;
    --white: #f4f4f4;
    --badge: #f07d1a;
    --badge-ring: #8a8a8a;
  }
  * { box-sizing: border-box; margin: 0; padding: 0; }
  html, body { width: 1200px; height: 780px; overflow: hidden; background: var(--stage); }
  .canvas { position: relative; width: 1200px; height: 780px; }
  .card {
    position: absolute; top: 110px; width: 340px; height: 560px;
    background: var(--card); border-radius: 22px;
    box-shadow: 0 18px 40px rgba(0,0,0,.55);
    overflow: hidden;
  }
  .card-front { left: 215px; }
  .card-back { left: 645px; }

  /* front */
  .front-mark {
    position: absolute; left: 0; right: 0; top: 200px;
    display: flex; flex-direction: column; align-items: center; gap: 26px;
  }
  .front-mark .brand-name {
    font-family: "Exo 2", sans-serif; font-weight: 700; font-size: 64px;
    letter-spacing: 2px; color: var(--red);
  }
  .front-mark .brand-dot { width: 46px; height: 46px; border-radius: 50%; background: var(--gold); }

  /* back */
  .back-logo {
    position: absolute; top: 44px; left: 0; right: 0;
    display: flex; justify-content: center; align-items: center; gap: 12px;
  }
  .back-logo .brand-dot { width: 18px; height: 18px; border-radius: 50%; background: var(--gold); }
  .back-logo .brand-name {
    font-family: "Exo 2", sans-serif; font-weight: 700; font-size: 40px;
    letter-spacing: 1px; color: var(--red);
  }
  .person { position: absolute; top: 158px; left: 0; right: 0; text-align: center; }
  .person-name {
    font-family: "Exo 2", sans-serif; font-weight: 700; font-size: 30px; color: var(--red); line-height: 1;
  }
  .person-role {
    margin-top: 6px; font-family: "Open Sans", sans-serif; font-weight: 600;
    font-size: 13px; color: var(--white); letter-spacing: .4px;
  }
  .rule-row {
    position: absolute; left: 26px; right: 26px; display: flex; align-items: center; gap: 8px;
  }
  .rule-row .rule { flex: 1; height: 2px; background: var(--red); }
  .icon-chip {
    width: 22px; height: 22px; background: var(--red); border-radius: 5px;
    transform: rotate(45deg); display: flex; align-items: center; justify-content: center;
  }
  .icon-chip svg { transform: rotate(-45deg); width: 13px; height: 13px; }
  .rule-icons { top: 234px; }
  .rule-divider { top: 348px; }
  .contact-list {
    position: absolute; top: 262px; left: 0; right: 0; list-style: none; text-align: center;
    font-family: "Open Sans", sans-serif; font-size: 13.5px; line-height: 16.5px; color: var(--white);
  }
  .address {
    position: absolute; top: 386px; left: 0; right: 0; text-align: center;
    font-family: "Open Sans", sans-serif; font-size: 14px; line-height: 18px; color: var(--white);
  }
  .cert-row {
    position: absolute; top: 438px; right: 30px; display: flex; gap: 12px;
  }
  .cert-badge {
    width: 34px; height: 34px; border-radius: 50%; background: var(--badge);
    border: 3px solid var(--badge-ring);
  }
  .member-badge {
    position: absolute; top: 470px; left: 30px; width: 52px; height: 30px;
    border-radius: 15px 15px 4px 4px; background: var(--white);
  }
  .partner-band {
    position: absolute; left: 24px; right: 24px; bottom: 20px; height: 38px;
    display: flex; border: 2px solid var(--red); border-radius: 3px; overflow: hidden;
  }
  .partner-band .band-client {
    flex: 1.3; display: flex; align-items: center; justify-content: center;
    font-family: "Exo 2", sans-serif; font-weight: 600; font-size: 14px; color: var(--red);
  }
  .partner-band .band-partner {
    flex: 1; background: var(--red); display: flex; align-items: center; justify-content: center;
    font-family: "Exo 2", sans-serif; font-weight: 600; font-size: 14px; color: var(--white);
  }
</style>
</head>
<body>
<div class="canvas">

  <section class="card card-front" aria-label="Card front">
    <div class="front-mark">
      <span class="brand-name">KELVANE</span>
      <span class="brand-dot"></span>
    </div>
  </section>

  <section class="card card-back" aria-label="Card back">
    <div class="back-logo">
      <span class="brand-dot"></span>
      <span class="brand-name">KELVANE</span>
    </div>

    <div class="person">
      <p class="person-name">Mara Voskuil</p>
      <p class="person-role">Administration Executive</p>
    </div>

    <div class="rule-row rule-icons">
      <span class="rule"></span>
      <span class="icon-chip"><svg viewBox="0 0 16 16"><path fill="#fff" d="M4 1l3 3-2 2c1 2 3 4 5 5l2-2 3 3-2 2C7 14 2 9 2 3z"/></svg></span>
      <span class="icon-chip"><svg viewBox="0 0 16 16"><path fill="#fff" d="M4 1h8v4H4zM2 6h12v6h-2v3H4v-3H2zM5 10v3h6v-3z"/></svg></span>
      <span class="icon-chip"><svg viewBox="0 0 16 16"><path fill="#fff" d="M1 3h14v10H1zM2.5 4.5L8 9l5.5-4.5" stroke="#e92b26" stroke-width="1.2"/></svg></span>
      <span class="icon-chip"><svg viewBox="0 0 16 16"><circle cx="8" cy="8" r="6.5" fill="none" stroke="#fff" stroke-width="1.5"/><path d="M1.5 8h13M8 1.5c-3 3-3 10 0 13M8 1.5c3 3 3 10 0 13" fill="none" stroke="#fff" stroke-width="1.2"/></svg></span>
      <span class="rule"></span>
    </div>

    <ul class="contact-list">
      <li>1300 472 615 (Phone)</li>
      <li>+61 412 908 374 (Mobile)</li>
      <li>+61 8 9204 6651 (Fax)</li>
      <li>mara.voskuil@kelvane.com</li>
      <li>www.kelvane.com</li>
    </ul>

    <div class="rule-row rule-divider">
      <span class="rule"></span>
      <span class="icon-chip"><svg viewBox="0 0 16 16"><path fill="#fff" d="M8 1a5 5 0 0 1 5 5c0 4-5 9-5 9S3 10 3 6a5 5 0 0 1 5-5zm0 3a2 2 0 1 0 0 4 2 2 0 0 0 0-4z"/></svg></span>
      <span class="rule"></span>
    </div>

    <p class="address">48 Depot Crescent<br>Marlow, WA 6190</p>

    <div class="cert-row">
      <span class="cert-badge"></span>
      <span class="cert-badge"></span>
      <span class="cert-badge"></span>
    </div>
    <span class="member-badge"></span>

    <div class="partner-band">
      <span class="band-client">Kelvane</span>
      <span class="band-partner">Petrava</span>
    </div>
  </section>

</div>
</body>
</html>
```